Tolvik Commercial Cleaning is lookong for a new business card design.

A fresh new design that's professional and stylish. We need a serious upgrade to our business cards. I have included pictures of our existing ones. Our clients include professional individuals and business owners. We woupdblike something professional and upbeat. Please have fun and see what you come uo with.

Target Market(s)

Property managers, business owners, facility managers and other similar professionals

Industry/Entity Type

Janitorial

Contact Information for Business Card

Name, cell, office number, email, web address

Font styles to use
Sans Serif

Colors

Designer to choose colors to be used in the design.

Requirements
Must have
• please use the green color in our logo
Nice to have
• Bar code
Should not have
• Address

```html
<!DOCTYPE html>
<html lang="en">
<head>
<meta charset="utf-8">
<title>Tolvik Commercial Cleaning – Business Card</title>
<link rel="stylesheet" href="https://fonts.googleapis.com/css2?family=Arimo:wght@400;700&display=swap">
<style>
  :root {
    --brand-green: #2fa84f;
    --deep-green: #25903f;
    --brand-blue: #2b4c9b;
    --paper: #f6f6f6;
    --backdrop: #dcdcdc;
    --ink-light: #ffffff;
  }
  * { box-sizing: border-box; margin: 0; padding: 0; }
  html, body { width: 1200px; height: 800px; overflow: hidden; }
  body {
    background: var(--backdrop);
    font-family: "Arimo", Arial, sans-serif;
    position: relative;
  }
  .card {
    position: absolute;
    width: 540px;
    height: 310px;
    border-radius: 22px;
    overflow: hidden;
    left: 330px;
  }
  .card--front { top: 70px; background: var(--paper); }
  .card--back { top: 420px; background: var(--brand-green); }

  .front-art { position: absolute; inset: 0; width: 100%; height: 100%; }

  .contact {
    position: absolute;
    left: 318px;
    top: 74px;
    color: var(--ink-light);
  }
  .contact__name {
    font-size: 24px;
    font-weight: 700;
    margin-bottom: 10px;
  }
  .contact__list { list-style: none; }
  .contact__item {
    display: flex;
    align-items: center;
    gap: 8px;
    font-size: 14px;
    line-height: 21px;
  }
  .contact__icon { width: 11px; height: 11px; flex: none; }

  .wordmark {
    position: absolute;
    left: 44px;
    bottom: 48px;
    color: var(--brand-green);
    font-weight: 700;
    line-height: 1.05;
  }
  .wordmark__name { display: block; font-size: 58px; letter-spacing: -1px; }
  .wordmark__line { display: block; font-size: 20px; }

  .back-mark {
    position: absolute;
    inset: 0;
    display: flex;
    flex-direction: column;
    align-items: center;
    justify-content: center;
    color: var(--deep-green);
    font-weight: 700;
    line-height: 1.05;
  }
  .back-mark__name { font-size: 84px; letter-spacing: -2px; }
  .back-mark__line { font-size: 24px; margin-top: 6px; }
</style>
</head>
<body>
  <section class="card card--front">
    <svg class="front-art" viewBox="0 0 540 310" aria-hidden="true">
      <circle cx="478" cy="58" r="262" fill="none" stroke="var(--brand-blue)" stroke-width="3"/>
      <circle cx="478" cy="58" r="254" fill="var(--brand-green)"/>
    </svg>

    <div class="contact">
      <p class="contact__name">Marcus Hale</p>
      <ul class="contact__list">
        <li class="contact__item">
          <svg class="contact__icon" viewBox="0 0 12 12" aria-hidden="true"><path d="M2.5 1l2 2.2-1 1.3c.7 1.6 2 2.9 3.5 3.6l1.3-1 2.2 2-1.2 1.6C5.5 10.5 1.5 6.5 1 2.2z" fill="currentColor"/></svg>
          (555) 014-2270
        </li>
        <li class="contact__item">
          <svg class="contact__icon" viewBox="0 0 12 12" aria-hidden="true"><rect x="1" y="2.5" width="10" height="7" fill="currentColor"/><path d="M1 2.5l5 4 5-4" fill="none" stroke="var(--brand-green)" stroke-width="1"/></svg>
          marcus@tolvikcleaning.com
        </li>
        <li class="contact__item">
          <svg class="contact__icon" viewBox="0 0 12 12" aria-hidden="true"><circle cx="6" cy="6" r="5" fill="currentColor"/><path d="M1 6h10M6 1c2 2.5 2 7.5 0 10M6 1c-2 2.5-2 7.5 0 10" fill="none" stroke="var(--brand-green)" stroke-width=".8"/></svg>
          www.tolvikcleaning.com
        </li>
      </ul>
    </div>

    <p class="wordmark">
      <span class="wordmark__name">Tolvik</span>
      <span class="wordmark__line">Commercial Cleaning</span>
    </p>
  </section>

  <section class="card card--back">
    <p class="back-mark">
      <span class="back-mark__name">Tolvik</span>
      <span class="back-mark__line">Commercial Cleaning</span>
    </p>
  </section>
</body>
</html>
```